A clean crisp business card for a Landscape Construction company. Designed to be easy to read contact/ info and also be appealing/interesting, unlike a traditional business card.

Industry/Entity Type

Landscape Construction

Contact Information for Business Card

Company name : Brambleford Landscape Construction, phone number: (877) 62Vista, website:Bramblefordyards.example, Email, sales@bramblefordyards.example

Requirements
Nice to have
• Luxurious finishes/ details…. Icons or emblems next to contact info
Should not have
• Clipart or general pictures

```html
<!DOCTYPE html>
<html lang="en">
<head>
<meta charset="utf-8">
<title>Brambleford Landscape Construction – Business Card</title>
<link rel="stylesheet" href="https://fonts.googleapis.com/css2?family=Cinzel:wght@500&family=Open+Sans:wght@400;600&display=swap">
<style>
  :root {
    --bg: #d4d6d8;
    --card-white: #ffffff;
    --leaf-green: #a0cc3a;
    --leaf-green-dark: #8dbb2c;
    --brand-blue: #2168b6;
    --ink: #1f1f1f;
  }
  * { box-sizing: border-box; margin: 0; padding: 0; }
  html, body {
    width: 1200px; height: 928px; overflow: hidden;
    background: var(--bg);
    font-family: "Open Sans", Arial, sans-serif;
  }
  .canvas { position: relative; width: 1200px; height: 928px; }
  .card {
    position: absolute; left: 265px; width: 672px; height: 384px;
    border-radius: 16px; overflow: hidden;
  }
  /* Back side */
  .card-back { top: 58px; background: var(--leaf-green); }
  .card-back .pattern {
    position: absolute; inset: 0;
    background: linear-gradient(100deg, var(--leaf-green-dark) 0%, var(--leaf-green) 50%, #b3d95c 100%);
  }
  .card-back .back-name {
    position: absolute; left: 0; right: 0; top: 172px;
    text-align: center; color: var(--card-white);
    font-weight: 600; font-size: 24px; letter-spacing: 0.5px;
  }
  /* Front side */
  .card-front { top: 484px; background: var(--card-white); }
  .brand {
    position: absolute; left: 40px; top: 86px;
    display: flex; align-items: center; gap: 12px;
    color: var(--brand-blue); font-weight: 600;
  }
  .brand-dot { width: 26px; height: 26px; border-radius: 50%; background: var(--leaf-green); flex: none; }
  .brand-name { font-size: 26px; line-height: 1.05; }
  .brand-name small { display: block; font-size: 12.5px; letter-spacing: 2.3px; text-transform: uppercase; margin-top: 4px; }
  .person { position: absolute; right: 38px; top: 112px; text-align: right; }
  .person-name { font-family: "Cinzel", Georgia, serif; font-size: 27px; font-weight: 500; letter-spacing: 1px; }
  .person-name .first { color: var(--brand-blue); }
  .person-name .last { color: var(--leaf-green); }
  .person-role { font-size: 15px; color: var(--ink); margin-top: 2px; letter-spacing: 0.4px; }
  .contacts { position: absolute; left: 42px; top: 216px; list-style: none; }
  .contacts li {
    display: flex; align-items: center; gap: 8px;
    font-size: 15.5px; color: var(--ink); height: 26px;
  }
  .contacts svg { width: 16px; height: 16px; fill: var(--leaf-green); flex: none; }
  .wave { position: absolute; left: 0; bottom: 0; width: 672px; height: 140px; }
  .address {
    position: absolute; right: 38px; bottom: 28px; text-align: right;
    color: var(--card-white); font-weight: 600; font-size: 15.5px; line-height: 27px;
  }
</style>
</head>
<body>
<div class="canvas">
  <section class="card card-back" aria-label="Card back">
    <div class="pattern" role="img" aria-label="Repeating embossed brand pattern on green"></div>
    <p class="back-name">Brambleford</p>
  </section>

  <section class="card card-front" aria-label="Card front">
    <div class="brand">
      <span class="brand-dot"></span>
      <p class="brand-name">Brambleford<small>Landscape Construction</small></p>
    </div>

    <div class="person">
      <p class="person-name"><span class="first">Dana</span> <span class="last">Whitlock</span></p>
      <p class="person-role">Director</p>
    </div>

    <ul class="contacts">
      <li>
        <svg viewBox="0 0 24 24" aria-hidden="true"><path d="M6.6 10.8a15.1 15.1 0 0 0 6.6 6.6l2.2-2.2a1 1 0 0 1 1-.25 11.4 11.4 0 0 0 3.6.57 1 1 0 0 1 1 1V20a1 1 0 0 1-1 1A17 17 0 0 1 3 4a1 1 0 0 1 1-1h3.5a1 1 0 0 1 1 1c0 1.25.2 2.45.57 3.57a1 1 0 0 1-.25 1z"/></svg>
        (877) 62Vista
      </li>
      <li>
        <svg viewBox="0 0 24 24" aria-hidden="true"><path d="M2 5h20v14H2z" opacity="0"/><path d="M2 5h20v2l-10 6L2 7zM2 9l10 6 10-6v10H2z"/></svg>
        sales@bramblefordyards.example
      </li>
      <li>
        <svg viewBox="0 0 24 24" aria-hidden="true"><circle cx="12" cy="12" r="10"/></svg>
        www.bramblefordyards.example
      </li>
    </ul>

    <svg class="wave" viewBox="0 0 672 140" preserveAspectRatio="none" aria-hidden="true">
      <path d="M0 20 C70 90 140 115 230 106 C380 90 520 22 672 14 V140 H0 Z" fill="var(--leaf-green)"/>
      <path d="M0 26 C70 96 140 120 230 111 C380 96 520 30 672 22 V140 H0 Z" fill="var(--card-white)"/>
      <path d="M0 28 C70 98 140 122 230 113 C380 98 520 34 672 30 V140 H0 Z" fill="var(--brand-blue)"/>
    </svg>

    <address class="address" style="font-style:normal">
      4170 Orchard Hollow Rd<br>
      Suite 112, Fenwick, OH 45990
    </address>
  </section>
</div>
</body>
</html>
```